Podiatry clinic requires a modern revamp and editing of existing website.

I would like a fresh new look and updated information for my current business website. An easy to navigate site with prominent address and phone number for call to action. We are a podiatry clinic that focuses on general and sports podiatry.
I would like 4 pages; including Home page, About Us, Services & Contact.
www.brambleridgepodiatry.net

Target Market(s)

Active working professionals.

Industry/Entity Type

Medical

Coding

Coded - Design and coding required

Number of Pages Required

4 page

Font styles to use
Sans Serif

Colors
6b449b

Requirements
Must have
• A modern look with logo and active images; clean and uncluttered. Visible phone number and address for call to action.
• 4 pages - Home, About Us, Services, Contact.
• Home page - update address & service logos.
• About Us - update of personal information.
• Services - Revamp of existing page.
• Contact page to include Google map, email & phone number.
Nice to have
• Ability to add content easily; eg. a blog or adding video onto Home page.
• Link to Facebook page.

```html
<!DOCTYPE html>
<html lang="en">
<head>
<meta charset="utf-8">
<title>Bramble Ridge Podiatry</title>
<link rel="stylesheet" href="https://fonts.googleapis.com/css2?family=Lato:wght@400;700;900&family=Raleway:wght@400;700&display=swap">
<style>
:root{
  --purple:#4b2d8f;
  --purple-soft:#9b86c8;
  --ink:#222;
  --text:#444;
  --rule:#cfcfcf;
  --footer:#393939;
  --footer-deep:#1f1f1f;
  --footer-text:#e6e6e6;
  --white:#fff;
}
*{margin:0;padding:0;box-sizing:border-box}
html,body{width:712px;height:1200px;overflow:hidden;background:var(--white)}
body{font-family:"Lato",sans-serif;color:var(--text)}
.page{position:relative;width:712px;height:1200px;overflow:hidden}
.abs{position:absolute}

/* top bar */
.topbar{left:0;top:0;width:712px;height:18px;background:var(--purple)}
.social{top:4px;display:flex;gap:10px;left:340px}
.social span{width:9px;height:9px;border-radius:50%;background:rgba(255,255,255,.85)}
.topbar-contact{top:0;height:18px;display:flex;align-items:center;gap:5px;color:var(--white);font-size:8px}
.topbar-contact .ico{width:16px;height:18px;background:#111;display:flex;align-items:center;justify-content:center}
.tb-phone{left:428px}
.tb-mail{left:516px}

/* header */
.brand{left:60px;top:28px;display:flex;align-items:center;gap:6px;font-family:"Lato",sans-serif;font-weight:900;font-size:17px;color:var(--purple);line-height:1}
.brand .dot{width:18px;height:18px;border-radius:50%;background:var(--purple)}
.nav{top:36px;left:298px;display:flex;align-items:center;font-size:8.5px;color:var(--purple)}
.nav a{color:var(--purple);text-decoration:none;height:25px;display:flex;align-items:center;padding:0 12px}
.nav a.active{border:1px solid var(--purple);font-weight:700;padding:0 14px;margin-right:0}
.book{left:534px;top:36px;width:120px;height:25px;background:var(--purple);color:var(--white);font-size:9px;font-weight:700;display:flex;align-items:center;justify-content:center;gap:6px}

/* hero */
.hero{left:0;top:80px;width:712px;height:280px;background:linear-gradient(135deg,#c9ced2 0%,#8a8f94 45%,#4c5156 75%,#2f3337 100%)}
.hero-arrow{top:134px;width:16px;height:16px;border:1px solid var(--white);border-radius:2px;display:flex;align-items:center;justify-content:center}
.hero-title{left:0;top:328px;width:712px;text-align:center;color:var(--white);font-weight:700;font-size:18px;font-family:"Lato",sans-serif}

/* section headings */
.heading{left:0;width:712px;text-align:center;font-family:"Raleway",sans-serif;font-size:22px;color:var(--ink)}
.heading b{color:var(--purple);font-weight:700}
.heading-rule{height:1px;background:var(--rule)}

.intro{left:94px;top:434px;width:524px;text-align:center;font-size:8px;line-height:14.6px;color:var(--text)}

/* services */
.services-bg{left:0;top:550px;width:712px;height:237px;background:linear-gradient(180deg,#4a4f48 0%,#30352f 55%,#3b3a33 100%)}
.services-title{left:0;top:572px;width:712px;text-align:center;color:var(--white);font-family:"Raleway",sans-serif;font-size:21px}
.services-rule{left:265px;top:602px;width:183px;height:1px;background:rgba(255,255,255,.6)}
.svc-head{top:622px;color:var(--white);font-weight:700;font-size:12px;text-decoration:underline}
.svc-divider{left:366px;top:624px;width:1px;height:102px;background:rgba(255,255,255,.3)}
.svc{color:var(--white);font-size:9px;display:flex;align-items:center;gap:6px}
.svc svg{flex:none}
.read-more{left:323px;top:744px;width:60px;height:20px;background:var(--purple-soft);color:var(--white);font-size:8px;font-weight:700;display:flex;align-items:center;justify-content:center}

/* review */
.quote-mark{font-family:"Raleway",sans-serif;font-weight:700;font-size:58px;color:#cfcfcf;line-height:1}
.review-text{left:128px;top:856px;width:456px;text-align:center;font-size:8px;line-height:14.5px;color:var(--text)}
.reviewer{left:0;top:910px;width:712px;text-align:center;color:var(--purple-soft);font-weight:700;font-size:9px}
.avatar{border-radius:50%;background:radial-gradient(circle at 50% 40%,#e2c8b6 0%,#b89484 55%,#7d6a62 100%)}
.avatar.current{border:2px solid var(--purple);background:radial-gradient(circle at 50% 40%,#e6d2c4 0%,#a9b7c9 60%,#7f90a5 100%)}

/* footer */
.footer{left:0;top:1026px;width:712px;height:148px;background:var(--footer)}
.f-title{top:1052px;color:var(--white);font-weight:700;font-size:9.5px}
.f-rule{height:1px;background:#5a5a5a}
.f-vrule{top:1042px;width:1px;height:104px;background:#4d4d4d}
.f-list{left:58px;top:1070px;width:72px;list-style:none;font-size:7px;color:var(--footer-text)}
.f-list li{height:20px;display:flex;align-items:center;gap:5px;border-bottom:1px solid #555}
.f-list li:last-child{border-bottom:none}
.f-contact{left:190px;color:var(--footer-text);font-size:7px;line-height:10.5px;display:flex;gap:6px}
.map{left:368px;top:1079px;width:134px;height:66px;background:linear-gradient(135deg,#e6e3d8 0%,#d4dbe2 50%,#c9dcc4 100%)}
.f-brand{left:560px;top:1098px;display:flex;align-items:center;gap:5px;color:#7c7c7c;font-weight:900;font-size:13px}
.f-brand .dot{width:14px;height:14px;border-radius:50%;background:#7c7c7c}
.copyright{left:0;top:1174px;width:712px;height:26px;background:var(--footer-deep);color:var(--footer-text);font-size:8px;display:flex;align-items:center;justify-content:center;gap:3px}
.copyright b{color:var(--white)}
</style>
</head>
<body>
<div class="page">

  <!-- top bar -->
  <div class="abs topbar"></div>
  <div class="abs social" aria-label="Social links"><span></span><span></span><span></span><span></span></div>
  <div class="abs topbar-contact tb-phone">
    <span class="ico"><svg width="8" height="8" viewBox="0 0 10 10"><path d="M2 1l2 2-1 1.2c.6 1.3 1.5 2.2 2.8 2.8L7 6l2 2-1.3 1.3C4.8 9 1 5.2.7 2.3z" fill="#fff"/></svg></span>
    555-214-7093
  </div>
  <div class="abs topbar-contact tb-mail">
    <span class="ico"><svg width="9" height="7" viewBox="0 0 10 8"><rect width="10" height="8" fill="#fff"/><path d="M0 0l5 4 5-4" stroke="#111" fill="none"/></svg></span>
    hello@brambleridgepodiatry.net
  </div>

  <!-- header -->
  <div class="abs brand"><span class="dot"></span>Bramble Ridge<br>Podiatry</div>
  <nav class="abs nav">
    <a class="active" href="#">Home</a>
    <a href="#">About Us</a>
    <a href="#">Services</a>
    <a href="#">Contact</a>
  </nav>
  <div class="abs book">
    <svg width="12" height="12" viewBox="0 0 12 12"><circle cx="6" cy="3" r="2.5" fill="#fff"/><path d="M1 12c0-3 2.2-5 5-5s5 2 5 5z" fill="#fff"/></svg>
    Book Appointment
  </div>

  <!-- hero -->
  <div class="abs hero" role="img" aria-label="Runner's feet in sports shoes on a treadmill with the ankle joint highlighted"></div>
  <div class="abs hero-arrow" style="left:36px">
    <svg width="8" height="6" viewBox="0 0 8 6"><path d="M8 3H1M3 1L1 3l2 2" stroke="#fff" fill="none"/></svg>
  </div>
  <div class="abs hero-arrow" style="left:660px">
    <svg width="8" height="6" viewBox="0 0 8 6"><path d="M0 3h7M5 1l2 2-2 2" stroke="#fff" fill="none"/></svg>
  </div>
  <div class="abs hero-title">Bramble Ridge Podiatry is a Podiatry clinic in the heart of Ridgeford</div>

  <!-- welcome -->
  <h1 class="abs heading" style="top:390px">Welcome to <b>Bramble Ridge Podiatry</b></h1>
  <div class="abs heading-rule" style="left:165px;top:421px;width:382px"></div>
  <p class="abs intro">
    Bramble Ridge Podiatry is a Podiatry clinic in the heart of Ridgeford city centre. We are located between Fernlow &amp; Ashby Streets in the Fernlow Business Centre / Harbourview Complex.<br>
    Our podiatrists are fully qualified health professionals who are able to diagnose, treat, manage or help to prevent all medical conditions that affect the feet and lower limb.<br>
    We provide General Podiatry Treatment and some Specialised Services in relation to various foot conditions, including Sports Injuries, Orthotic Therapy and Nail Surgery.
  </p>

  <!-- services -->
  <div class="abs services-bg" role="img" aria-label="Close-up of a runner's shoe on a forest trail, darkened"></div>
  <h2 class="abs services-title">Our Services</h2>
  <div class="abs services-rule"></div>
  <div class="abs svc-head" style="left:144px">General Treatments</div>
  <div class="abs svc-head" style="left:431px">Specialised Treatments</div>
  <div class="abs svc-divider"></div>

  <svg width="0" height="0" style="position:absolute">
    <symbol id="tick" viewBox="0 0 11 11"><rect x=".75" y="1.75" width="8.5" height="8.5" fill="none" stroke="#fff" stroke-width="1.3"/><path d="M2.8 5.5l2 2L10.4.8" fill="none" stroke="#fff" stroke-width="1.6"/></symbol>
  </svg>

  <div class="abs svc" style="left:83px;top:654px"><svg width="11" height="11"><use href="#tick"/></svg>Nails</div>
  <div class="abs svc" style="left:164px;top:654px"><svg width="11" height="11"><use href="#tick"/></svg>Corns</div>
  <div class="abs svc" style="left:266px;top:654px"><svg width="11" height="11"><use href="#tick"/></svg>Callus</div>
  <div class="abs svc" style="left:83px;top:682px"><svg width="11" height="11"><use href="#tick"/></svg>Warts</div>
  <div class="abs svc" style="left:164px;top:682px"><svg width="11" height="11"><use href="#tick"/></svg>Skin Disorders</div>
  <div class="abs svc" style="left:266px;top:682px"><svg width="11" height="11"><use href="#tick"/></svg>Heel Pain</div>
  <div class="abs svc" style="left:83px;top:710px"><svg width="11" height="11"><use href="#tick"/></svg>Knee Pain</div>
  <div class="abs svc" style="left:164px;top:710px"><svg width="11" height="11"><use href="#tick"/></svg>Toe Deformities</div>

  <div class="abs svc" style="left:414px;top:654px"><svg width="11" height="11"><use href="#tick"/></svg>Diabetic Management</div>
  <div class="abs svc" style="left:555px;top:654px"><svg width="11" height="11"><use href="#tick"/></svg>Nail Surgery</div>
  <div class="abs svc" style="left:414px;top:682px"><svg width="11" height="11"><use href="#tick"/></svg>Gait Analysis</div>
  <div class="abs svc" style="left:555px;top:682px"><svg width="11" height="11"><use href="#tick"/></svg>Orthotic Therapy</div>
  <div class="abs svc" style="left:414px;top:710px"><svg width="11" height="11"><use href="#tick"/></svg>Biomechanical Assessment</div>

  <div class="abs read-more">Read More</div>

  <!-- review -->
  <h2 class="abs heading" style="top:806px">Customer <b>Review</b></h2>
  <div class="abs heading-rule" style="left:165px;top:844px;width:382px"></div>
  <div class="abs quote-mark" style="left:96px;top:852px">&ldquo;</div>
  <div class="abs quote-mark" style="left:588px;top:862px">&rdquo;</div>
  <p class="abs review-text">Fusce elementum, nulla vel pellentes consequat, ante nulla hendrerit arcu, ac tincidunt mauris lacus sed leo. vamus suscipit molestie vestibulum. Lorem ipsum dolor sit amet, Fusce elementum, nulla vel pellentes consequat, ante nulla hendrerit arcu, ac tincidunt mauris lacus sed leo. vamus suscipit molestie. Fusce elementum, nulla vel</p>
  <div class="abs reviewer">Mr. Lorem Ipsum</div>
  <div class="abs avatar" style="left:217px;top:943px;width:40px;height:40px" role="img" aria-label="Customer portrait"></div>
  <div class="abs avatar" style="left:273px;top:943px;width:40px;height:40px" role="img" aria-label="Customer portrait"></div>
  <div class="abs avatar current" style="left:329px;top:935px;width:57px;height:57px" role="img" aria-label="Portrait of the featured reviewer"></div>
  <div class="abs avatar" style="left:401px;top:943px;width:40px;height:40px" role="img" aria-label="Customer portrait"></div>
  <div class="abs avatar" style="left:457px;top:943px;width:40px;height:40px" role="img" aria-label="Customer portrait"></div>

  <!-- footer -->
  <div class="abs footer"></div>
  <div class="abs f-vrule" style="left:162px"></div>
  <div class="abs f-vrule" style="left:338px"></div>
  <div class="abs f-vrule" style="left:534px"></div>

  <div class="abs f-title" style="left:58px">Quick Links</div>
  <div class="abs f-rule" style="left:58px;top:1069px;width:72px"></div>
  <ul class="abs f-list">
    <li><svg width="3" height="5" viewBox="0 0 3 5"><path d="M0 0l3 2.5L0 5z" fill="#fff"/></svg>Home</li>
    <li><svg width="3" height="5" viewBox="0 0 3 5"><path d="M0 0l3 2.5L0 5z" fill="#fff"/></svg>About Us</li>
    <li><svg width="3" height="5" viewBox="0 0 3 5"><path d="M0 0l3 2.5L0 5z" fill="#fff"/></svg>Services</li>
    <li><svg width="3" height="5" viewBox="0 0 3 5"><path d="M0 0l3 2.5L0 5z" fill="#fff"/></svg>Contact</li>
  </ul>

  <div class="abs f-title" style="left:190px">Contact Details</div>
  <div class="abs f-rule" style="left:190px;top:1069px;width:110px"></div>
  <div class="abs f-contact" style="top:1077px">
    <svg width="6" height="8" viewBox="0 0 6 8"><path d="M3 8C1 5 0 4 0 3a3 3 0 016 0c0 1-1 2-3 5z" fill="#fff"/><circle cx="3" cy="3" r="1" fill="#393939"/></svg>
    <span>Suite 12 / 48 Fernlow Street<br>Ridgeford&nbsp; 4020</span>
  </div>
  <div class="abs f-rule" style="left:190px;top:1104px;width:110px"></div>
  <div class="abs f-contact" style="top:1110px">
    <svg width="7" height="7" viewBox="0 0 10 10"><path d="M2 1l2 2-1 1.2c.6 1.3 1.5 2.2 2.8 2.8L7 6l2 2-1.3 1.3C4.8 9 1 5.2.7 2.3z" fill="#fff"/></svg>
    <span>1300 482 907</span>
  </div>
  <div class="abs f-rule" style="left:190px;top:1127px;width:110px"></div>
  <div class="abs f-contact" style="top:1133px">
    <svg width="7" height="6" viewBox="0 0 10 8"><rect width="10" height="8" fill="#fff"/><path d="M0 0l5 4 5-4" stroke="#393939" fill="none"/></svg>
    <span>info@brambleridgepodiatry.net</span>
  </div>

  <div class="abs f-title" style="left:368px">Location Map</div>
  <div class="abs f-rule" style="left:368px;top:1069px;width:135px"></div>
  <div class="abs map" role="img" aria-label="Street map showing the clinic location"></div>

  <div class="abs f-brand"><span class="dot"></span>Bramble Ridge</div>

  <div class="abs copyright">Copyright &copy; 2016 <b>Bramble Ridge Podiatry</b>. All Rights Reserved.</div>
</div>
</body>
</html>
```